Buchcover-Design für Roman
Zielgruppe
Ich bin Autor und veröffentliche meinen ersten Roman.
Eine humoristische Geschichte voller Musik und Filmzitate.
Die Zielgruppe sind Erwachsene zwischen 30 und 40.
Aufgabenstellung
Titel: Die Welt dreht sich halt im Kreis
Autor: Tobias Hellenkamp
Bitte unbedingt auch die technischen Vorgaben beachten, siehe auch die Musterdatei, die ich hochgeladen habe.(Cover.PNG)
Technische Daten des Verlages:
Das Buch soll als Paperback und als Ebook gleichzeitig im KRU-Verlag erscheinen.
Das Paperback soll das Format 12 * 19 cm haben, also jeweils die Vorderseite und Rückseite.
Es werden ca. 380 Seiten dabei herauskommen.
Ich gehe von ca. 2,5 cm für den Buchrücken aus.
Laut Verlag muss die Farbdatei mindestens 300 dpi haben.
Das Format beträgt laut KRU: 275,1 mm * 200,0 mm .
Zusätzlich muss auf die Rückseite ein Barcode als PNG Datei eingefügt werden, der 144 dpi haben wird.
Vorläufiger Klappentext:
Markus Finkler, für seine Freunde, wenn er denn noch welche hätte, einfach nur Finki, ist ein nerdiger Verlierertyp, der in eine tiefe Sinnkrise stürzt. Verantwortlich dafür sind 3 Dinge, sein nahender 40. Geburtstag, der Tod seines Vaters und die Einladung zum Klassentreffen seiner alten Schule. Bisher hat er in seinem Leben noch nicht viel hinbekommen und sich auch deshalb von den Menschen entfernt. Er führt ein einsames Dasein, in seiner begrenzten Welt aus Filmen und Musik. Nun, auch mit 39 noch lange nicht erwachsen, muss er sich diesen Dingen stellen und sein Leben endlich auf die Reihe bekommen, wobei er natürlich von einer Katastrophe in die nächste stürzt.
Vorläufige Autoreninfo:
Der Autor wurde 1979 in Dortmund geboren und lebt seit 2017 mit seiner Familie in seiner Wahlheimat, dem beschaulichen Kempen am Niederrhein. Er ist hauptberuflich bei einem großen Finanzdienstleistungsunternehmen in Düsseldorf tätig, verwirklichte sich zu seinem 40. Geburtstag seinen lang gehegten Traum und begann nebenberuflich zu schreiben. Das hier vorliegende Produkt seiner Phantasie stellt seinen 1. Roman dar. Weitere sind in Planung.
Soll beides auf die Rückseite gedruck..

```html
<!DOCTYPE html>
<html lang="de">
<head>
<meta charset="utf-8">
<title>Die Welt dreht sich halt im Kreis – Buchcover</title>
<link href="https://fonts.googleapis.com/css2?family=Oswald:wght@600&family=Cinzel:wght@500&family=Open+Sans:wght@400;700&display=swap" rel="stylesheet">
<style>
  :root {
    --page-bg: #e6e6e6;
    --ink: #111111;
    --paper: #f1f1f1;
    --sky-light: #ececec;
    --sky-mid: #c9c9c9;
    --road-dark: #4a4a4a;
    --spine-black: #141414;
    --white: #ffffff;
    --body-text: #2a2a2a;
    --film-light: #d9d9d9;
    --film-mid: #a9a9a9;
    --film-dark: #7a7a7a;
  }
  * { margin: 0; padding: 0; box-sizing: border-box; }
  html, body { width: 1200px; height: 3187px; overflow: hidden; }
  body { background: var(--page-bg); position: relative; }

  .front-cover {
    position: relative;
    width: 76em;
    height: 120.3em;
    overflow: hidden;
    background: var(--paper);
  }
  .cover-photo {
    position: absolute; inset: 0;
    background:
      radial-gradient(ellipse 60% 45% at 72% 88%, rgba(60,60,60,.55), rgba(60,60,60,0) 70%),
      linear-gradient(180deg, var(--sky-light) 0%, #e2e2e2 40%, var(--sky-mid) 62%, #8a8a8a 82%, var(--road-dark) 100%);
  }
  .cover-title {
    position: absolute;
    top: 2.55em; left: 1.1em; right: 0.3em;
    font-family: "Oswald", "Arial Narrow", sans-serif;
    font-weight: 600;
    font-size: 11.5em;
    line-height: 1.02;
    text-align: center;
    text-transform: uppercase;
    letter-spacing: -0.01em;
    color: var(--ink);
    text-shadow: 0.03em 0.03em 0 var(--white), -0.02em -0.02em 0 var(--white), 0.05em 0.06em 0.06em rgba(0,0,0,.35);
  }
  .cover-title span { display: block; }
  .author-band {
    position: absolute;
    right: 0; bottom: 10em;
    width: 48em; height: 7em;
    background: var(--spine-black);
    border-radius: 3.5em 0 0 3.5em;
    display: flex; align-items: center; justify-content: center;
  }
  .author-band span {
    font-family: "Cinzel", Georgia, serif;
    font-weight: 500;
    font-size: 3.3em;
    color: var(--white);
    letter-spacing: 0.02em;
    text-transform: uppercase;
    white-space: nowrap;
  }

  .front-single {
    position: absolute;
    top: 140px; left: 182px;
    font-size: 11px;
    box-shadow: 0 10px 30px rgba(0,0,0,.18);
  }

  .cover-wrap {
    position: absolute;
    top: 1700px; left: 50px;
    width: 1100px; height: 788px;
    display: flex;
    box-shadow: 0 10px 30px rgba(0,0,0,.18);
  }
  .back-cover {
    position: relative;
    width: 498px; height: 788px;
    background: linear-gradient(180deg, #eeeeee 0%, #e6e6e6 45%, #dadada 100%);
    overflow: hidden;
  }
  .back-text {
    position: absolute; top: 32px; left: 30px; right: 30px;
    font-family: "Open Sans", Arial, sans-serif;
    color: var(--body-text);
    font-size: 12.2px;
    line-height: 1.5;
    z-index: 1;
  }
  .back-text h2 {
    font-size: 12.2px; font-weight: 700; margin-bottom: 4px; color: var(--ink);
  }
  .back-text p { margin-bottom: 16px; }
  .film-art {
    position: absolute; left: 0; right: 0; bottom: 0; height: 400px;
    background:
      radial-gradient(ellipse 70% 50% at 30% 70%, rgba(90,90,90,.35), rgba(90,90,90,0) 70%),
      linear-gradient(180deg, rgba(218,218,218,0) 0%, var(--film-light) 18%, var(--film-mid) 55%, var(--film-dark) 100%);
  }
  .barcode-area {
    position: absolute; left: 30px; bottom: 24px;
    width: 120px; height: 52px;
    background: var(--white);
  }
  .publisher-mark {
    position: absolute; right: 30px; bottom: 36px;
    display: flex; align-items: center; gap: 6px;
    font-family: "Open Sans", Arial, sans-serif;
    font-weight: 700; font-size: 16px; color: var(--white);
  }
  .publisher-mark i { width: 14px; height: 14px; background: var(--white); display: block; }

  .spine {
    position: relative;
    width: 104px; height: 788px;
    background: var(--spine-black);
    display: flex; align-items: center; justify-content: center;
  }
  .spine::before, .spine::after {
    content: ""; position: absolute; top: 6px; bottom: 6px; width: 0;
    border-left: 4px dashed var(--white);
  }
  .spine::before { left: 8px; }
  .spine::after { right: 8px; }
  .spine-text {
    writing-mode: vertical-rl;
    transform: rotate(180deg);
    font-family: "Cinzel", Georgia, serif;
    font-weight: 500;
    font-size: 23px;
    color: var(--white);
    text-transform: uppercase;
    white-space: nowrap;
    letter-spacing: 0.01em;
  }
  .spine-text .dash { margin: 14px 0; }

  .front-in-wrap { font-size: 6.553px; }
</style>
</head>
<body>

  <section class="front-cover front-single">
    <div class="cover-photo" role="img" aria-label="Schwarzweißfoto: einsame Gestalt auf einer geschwungenen Straße im Nebel"></div>
    <h1 class="cover-title"><span>Die Welt</span><span>dreht sich</span><span>halt im</span><span>Kreis</span></h1>
    <div class="author-band"><span>Tobias Hellenkamp</span></div>
  </section>

  <section class="cover-wrap">
    <div class="back-cover">
      <div class="film-art" role="img" aria-label="Verblasste Filmstreifen-Illustration in Grautönen"></div>
      <div class="back-text">
        <h2>DAS BUCH:</h2>
        <p>Markus Finkler, für seine Freunde, wenn er denn noch welche hätte, einfach nur Finki, ist ein nerdiger Verlierertyp, der in eine tiefe Sinnkrise stürzt. Verantwortlich dafür sind 3 Dinge, sein nahender 40. Geburtstag, der Tod seines Vaters und die Einladung zum Klassentreffen seiner alten Schule. Bisher hat er in seinem Leben noch nicht viel hinbekommen und sich auch deshalb von den Menschen entfernt. Er führt ein einsames Dasein, in seiner begrenzten Welt aus Filmen und Musik. Nun, auch mit 39 noch lange nicht erwachsen, muss er sich diesen Dingen stellen und sein Leben endlich auf die Reihe bekommen, wobei er natürlich von einer Katastrophe in die nächste stürzt.</p>
        <h2>DER AUTOR:</h2>
        <p>Der Autor wurde 1979 in Dortmund geboren und lebt seit 2017 mit seiner Familie in seiner Wahlheimat, dem beschaulichen Kempen am Niederrhein. Er ist hauptberuflich bei einem großen Finanzdienstleistungsunternehmen in Düsseldorf tätig, verwirklichte sich zu seinem 40. Geburtstag seinen lang gehegten Traum und begann nebenberuflich zu schreiben. Das hier vorliegende Produkt seiner Phantasie stellt seinen 1. Roman dar. Weitere sind in Planung.</p>
      </div>
      <div class="barcode-area" role="img" aria-label="Freifläche für den Barcode"></div>
      <div class="publisher-mark"><i></i>KRU</div>
    </div>

    <div class="spine">
      <div class="spine-text">Tobias Hellenkamp<span class="dash"> – </span>Die Welt dreht sich halt im Kreis</div>
    </div>

    <div class="front-cover front-in-wrap">
      <div class="cover-photo" role="img" aria-label="Schwarzweißfoto: einsame Gestalt auf einer geschwungenen Straße im Nebel"></div>
      <h1 class="cover-title"><span>Die Welt</span><span>dreht sich</span><span>halt im</span><span>Kreis</span></h1>
      <div class="author-band"><span>Tobias Hellenkamp</span></div>
    </div>
  </section>

</body>
</html>
```